Beacon Advisory Website

I currently have a website www.beaconadvisoryinc.com. We are a IT Consulting Company. Our website will pretty much tell out our services. I am looking to enhance my website and make it look more professional. Looking for very classy and Contemporary look and design for my website.

It Company

```html
<!DOCTYPE html>
<html lang="en">
<head>
<meta charset="utf-8">
<title>Beacon Advisory</title>
<link href="https://fonts.googleapis.com/css2?family=Roboto:wght@400;500;700&family=Open+Sans:ital,wght@0,400;0,600;1,400&display=swap" rel="stylesheet">
<style>
:root{
  --blue:#1a9fd9;
  --navy:#1b5d9b;
  --band:#2a6aa8;
  --ink:#333a40;
  --muted:#6b7075;
  --light:#f4f6f8;
  --line:#e6e8eb;
  --dark:#1e2023;
  --darker:#161719;
  --footText:#9a9ea3;
}
*{box-sizing:border-box;margin:0;padding:0}
html,body{width:1200px;height:2308px;overflow:hidden}
body{position:relative;background:#fff;font-family:"Open Sans",Arial,sans-serif;color:var(--ink)}
.abs{position:absolute}
a{color:inherit;text-decoration:none}

/* top bar */
.topbar{left:0;top:0;width:1200px;height:38px;background:var(--light)}
.social{display:flex;gap:21px;position:absolute;left:98px;top:13px}
.social span{width:11px;height:11px;border-radius:50%;background:var(--blue);display:block}
.contact-top{position:absolute;right:98px;top:11px;font:11px "Open Sans",sans-serif;color:var(--ink);display:flex;gap:26px;align-items:center}
.contact-top em{font-style:normal;color:var(--blue)}
.contact-top svg{vertical-align:-3px;margin-right:6px}

/* header */
.header{left:0;top:38px;width:1200px;height:114px;background:#fff;border-bottom:1px solid var(--line)}
.brand{position:absolute;left:98px;top:34px;display:flex;align-items:center;gap:10px;font:700 24px Roboto,sans-serif;color:var(--navy)}
.brand i{width:40px;height:40px;background:var(--navy);display:block;border-radius:4px}
.nav{position:absolute;left:370px;top:0;display:flex;height:114px}
.nav a{font:500 11px Roboto,sans-serif;color:#444;text-transform:uppercase;display:flex;align-items:center;justify-content:center;width:110px;position:relative}
.nav a.active{color:var(--blue)}
.nav a.active::after{content:"";position:absolute;bottom:0;left:0;right:0;height:3px;background:var(--blue)}
.nav a.active::before{content:"";position:absolute;bottom:3px;left:50%;margin-left:-5px;border:5px solid transparent;border-bottom-color:var(--blue)}

/* hero */
.hero{left:0;top:152px;width:1200px;height:516px;background:linear-gradient(100deg,#aab8c8 0%,#c9d3de 35%,#2a2f38 62%,#1b2029 100%)}
.hero-caption{position:absolute;left:98px;top:178px;width:479px;height:157px;background:rgba(20,30,45,.72);padding:20px 18px}
.hero-caption h1{font:700 28px Roboto,sans-serif;color:#fff;letter-spacing:.2px}
.hero-caption h2{font:400 15px Roboto,sans-serif;color:#fff;margin-top:8px}
.hero-caption p{font:12.5px/23px "Open Sans",sans-serif;color:#e8eef4;margin-top:8px}
.arrows{position:absolute;left:99px;top:438px;display:flex;gap:7px}
.arrows span{width:28px;height:28px;border:2px solid rgba(255,255,255,.8);border-radius:50%;display:flex;align-items:center;justify-content:center}

/* welcome */
.title{font:400 24px Roboto,sans-serif;color:var(--blue);display:flex;align-items:center;justify-content:center;gap:12px;width:1200px;left:0}
.title i{width:30px;height:30px;background:var(--navy);border-radius:4px;display:block}
.welcome-text{left:190px;width:820px;top:760px;text-align:center;font:11.5px/24px "Open Sans",sans-serif;color:var(--muted)}
.btns{left:0;width:1200px;top:849px;display:flex;justify-content:center;gap:6px}
.btn{font:500 12px Roboto,sans-serif;color:#fff;height:39px;padding:0 15px;display:flex;align-items:center;border-radius:2px}
.btn.navy{background:var(--navy);width:147px;justify-content:center}
.btn.sky{background:var(--blue);width:147px;justify-content:center}

/* features */
.features{left:98px;top:935px;width:1004px;display:flex}
.feature{flex:1;text-align:center;border-right:1px solid var(--line);padding:0 14px;height:210px}
.feature:last-child{border-right:none}
.feature .icon{width:78px;height:78px;border-radius:50%;background:#f1f3f5;margin:5px auto 0;display:flex;align-items:center;justify-content:center}
.feature .icon.on{background:var(--blue)}
.feature h3{font:500 14px Roboto,sans-serif;margin-top:22px;color:#222}
.feature h3.on{color:var(--blue)}
.feature p{font:11px/21.5px "Open Sans",sans-serif;color:var(--muted);margin:8px auto 0;width:300px}
.feature a{font:600 11px "Open Sans",sans-serif;color:var(--navy);text-decoration:underline;display:inline-block;margin-top:8px}

/* band */
.band{left:0;top:1190px;width:1200px;height:225px;background:linear-gradient(90deg,#2b6aa6,#3a7cb8 50%,#2b66a0)}
.notch{position:absolute;left:50%;margin-left:-16px;border:16px solid transparent}
.notch.top{top:0;border-top-color:#fff;border-bottom:none;border-left-width:16px;border-right-width:16px;height:0}
.notch.bottom{bottom:0;border-bottom-color:#fff;border-top:none}
.band h2{position:absolute;top:42px;width:1200px;text-align:center;font:400 24px Roboto,sans-serif;color:#fff}
.band p{position:absolute;top:78px;left:200px;width:800px;text-align:center;font:italic 11.5px/22px "Open Sans",sans-serif;color:#fff}
.subscribe{position:absolute;left:337px;top:139px;display:flex;height:37px}
.subscribe .field{width:404px;background:#fff;border-radius:18px 0 0 18px;font:11px "Open Sans",sans-serif;color:#888;display:flex;align-items:center;padding-left:18px;gap:8px}
.subscribe .go{width:122px;background:var(--blue);border-radius:0 18px 18px 0;font:500 12px Roboto,sans-serif;color:#fff;display:flex;align-items:center;justify-content:center}

/* services */
.carousel-nav{left:1083px;top:1473px;font:14px Roboto,sans-serif;color:#999;letter-spacing:6px}
.cards{left:98px;top:1524px;width:1004px;display:flex;gap:31px}
.card{width:314px;height:361px;border:1px solid var(--line);padding:6px 6px 0;text-align:center;box-shadow:0 1px 3px rgba(0,0,0,.04)}
.card .photo{height:182px}
.card h3{font:500 14px Roboto,sans-serif;color:var(--blue);margin-top:19px}
.card p{font:11px/21.5px "Open Sans",sans-serif;color:var(--muted);width:270px;margin:7px auto 0}
.card .btn{margin:18px auto 0;width:112px;height:32px;justify-content:center;background:var(--navy)}

/* partners */
.partners{left:0;top:1932px;width:1200px;height:95px;background:var(--light);display:flex;justify-content:center;align-items:center;gap:62px}
.partners span{width:118px;height:38px;background:#d6dade;border-radius:4px;display:block}

/* footer */
.footer{left:0;top:2027px;width:1200px;height:228px;background:var(--dark)}
.footer h4{position:absolute;top:34px;font:500 13.5px Roboto,sans-serif;color:#fff}
.footer .col{position:absolute;top:0}
.fbrand{position:absolute;top:82px;display:flex;align-items:center;gap:10px;font:700 24px Roboto,sans-serif;color:#8a8e93}
.fbrand i{width:40px;height:40px;background:#4a4e53;border-radius:4px;display:block}
.ftext{font:11px/22px "Open Sans",sans-serif;color:var(--footText)}
.menu li{list-style:none;font:11px/19.5px "Open Sans",sans-serif;color:var(--footText)}
.menu li::before{content:"›";margin-right:10px}
.post{font:11px/19px "Open Sans",sans-serif;color:var(--footText);width:215px;padding-bottom:6px;border-bottom:1px solid #3a3d41;margin-bottom:8px}
.post b{font-weight:400;color:#cfd2d5;display:block}
.post:last-child{border:none}
.touch{font:11px/19px "Open Sans",sans-serif;color:var(--footText);display:flex;gap:12px;margin-bottom:16px}
.touch i{width:8px;height:8px;border-radius:50%;background:#6a6e73;display:block;margin-top:5px;flex:none}
.bottom{left:0;top:2255px;width:1200px;height:53px;background:var(--darker)}
.bottom p{position:absolute;left:98px;top:20px;font:11px "Open Sans",sans-serif;color:var(--footText)}
.bottom .social{left:auto;right:70px;top:22px;gap:27px}
.bottom .social span{background:#6a6e73}
</style>
</head>
<body>

<div class="abs topbar">
  <div class="social"><span></span><span></span><span></span><span></span><span></span></div>
  <div class="contact-top">
    <span><svg width="16" height="11" viewBox="0 0 16 11"><rect x=".5" y=".5" width="15" height="10" fill="none" stroke="#1b5d9b"/><path d="M.5 .5 8 6l7.5-5.5" fill="none" stroke="#1b5d9b"/></svg>E-Mail:<em>info@beaconadvisoryinc.com</em></span>
    <span><svg width="13" height="13" viewBox="0 0 24 24"><path d="M6.6 10.8a15 15 0 0 0 6.6 6.6l2.2-2.2c.3-.3.7-.4 1-.2 1.1.4 2.3.6 3.6.6.6 0 1 .4 1 1V20c0 .6-.4 1-1 1A17 17 0 0 1 3 4c0-.6.4-1 1-1h3.5c.6 0 1 .4 1 1 0 1.3.2 2.5.6 3.6.1.3 0 .7-.2 1z" fill="#1b5d9b"/></svg>Phone: <em>+1 (555) 014 2290</em></span>
  </div>
</div>

<header class="abs header">
  <div class="brand"><i></i>Beacon Advisory</div>
  <nav class="nav">
    <a class="active">Home</a><a>Company</a><a>Services</a><a>Solutions</a><a>Resources</a><a>Career</a><a>Contact Us</a>
  </nav>
</header>

<section class="abs hero" role="img" aria-label="Photo of a businessman in a dark suit extending a hand for a handshake, blurred office team behind">
  <div class="hero-caption">
    <h1>MANAGEMENT PROFESSIONALS</h1>
    <h2>BEACON ADVISORY</h2>
    <p>Management Professionals from around the world and cultivating<br>key partnerships with corporations to understand their business</p>
  </div>
  <div class="arrows">
    <span><svg width="10" height="10" viewBox="0 0 10 10"><path d="M6.5 1 2.5 5l4 4" fill="none" stroke="#fff" stroke-width="1.6"/></svg></span>
    <span><svg width="10" height="10" viewBox="0 0 10 10"><path d="M3.5 1l4 4-4 4" fill="none" stroke="#fff" stroke-width="1.6"/></svg></span>
  </div>
</section>

<h2 class="abs title" style="top:707px"><i></i>Welcome to Beacon Advisory</h2>
<p class="abs welcome-text">Today's IT market is a dynamic, fast-paced industry, with ever-increasing demands. Meeting these demands for over 25 years, Beacon Advisory maintains a global presence, aggressively recruiting expertly qualified IT and Management Professionals from around the world and cultivating key partnerships with corporations to understand their business models end-to-end, with a goal of delivering exceptional client service...</p>
<div class="abs btns"><a class="btn navy">Click Read More Here</a><a class="btn sky">Get Consulting Today</a></div>

<div class="abs features">
  <div class="feature">
    <div class="icon on"><svg width="32" height="26" viewBox="0 0 32 26" fill="#fff"><circle cx="16" cy="7" r="5"/><path d="M7 24c0-6 4-9 9-9s9 3 9 9z"/><circle cx="6" cy="9" r="3.5"/><circle cx="26" cy="9" r="3.5"/><path d="M0 22c0-4 2.5-7 6-7 1.5 0 2.6.4 3.4 1C7 18 6.3 20 6.2 22zM32 22c0-4-2.5-7-6-7-1.5 0-2.6.4-3.4 1 2.4 2 3.1 4 3.2 6z"/></svg></div>
    <h3 class="on">Consulting</h3>
    <p>Beacon Advisory has certified professional consultants to work with you to help increase the business by providing IT services ...</p>
    <a>Read More info!</a>
  </div>
  <div class="feature">
    <div class="icon"><svg width="30" height="28" viewBox="0 0 30 28" fill="none" stroke="#1b5d9b" stroke-width="2.4"><circle cx="11" cy="15" r="5"/><circle cx="11" cy="15" r="8.5" stroke-dasharray="3.2 3"/><circle cx="23" cy="7" r="3"/><circle cx="23" cy="7" r="5.5" stroke-dasharray="2.4 2.2"/></svg></div>
    <h3>Staff Augmentation</h3>
    <p>Beacon Advisory has certified professional consultants to work with you to help increase the business by providing IT services ...</p>
    <a>Read More info!</a>
  </div>
  <div class="feature">
    <div class="icon"><svg width="30" height="22" viewBox="0 0 30 22" fill="none" stroke="#1b5d9b" stroke-width="2"><rect x="5" y="2" width="20" height="14" rx="1"/><path d="M1 19h28"/></svg></div>
    <h3>Offshore</h3>
    <p>Beacon Advisory has certified professional consultants to work with you to help increase the business by providing IT services ...</p>
    <a>Read More info!</a>
  </div>
</div>

<section class="abs band" role="img" aria-label="Blue-tinted photo of business people silhouettes in an office">
  <span class="notch top"></span>
  <h2>Free Consulting</h2>
  <p>Sed ut perspiciatis unde omnis iste natus error sit voluptatem accusantium doloremque laudantium, totam rem aperiam, eaque ipsa quae ab illo inventore veritatis et quasi architecto beatae vitae dicta sunt explicabo. Nemo enim ipsam voluptatem quia voluptas...</p>
  <div class="subscribe">
    <div class="field"><svg width="11" height="8" viewBox="0 0 11 8"><rect x=".5" y=".5" width="10" height="7" fill="none" stroke="#888"/><path d="M.5 .5 5.5 4.5l5-4" fill="none" stroke="#888"/></svg>Enter your Valid e-mail Addres</div>
    <div class="go">SUBSCRIBE</div>
  </div>
  <span class="notch bottom"></span>
</section>

<h2 class="abs title" style="top:1463px"><i></i>Our Services</h2>
<div class="abs carousel-nav">‹ ›</div>

<div class="abs cards">
  <div class="card">
    <div class="photo" role="img" aria-label="Photo of hands typing on a laptop keyboard" style="background:linear-gradient(135deg,#c9ced4,#8a9098 60%,#3c4148)"></div>
    <h3>Technology</h3>
    <p>Beacon Advisory Training programs are perfect for individuals to enhance their careers. Our hands-on practical and...</p>
    <a class="btn">Read More</a>
  </div>
  <div class="card">
    <div class="photo" role="img" aria-label="Photo of two businessmen reviewing a tablet together" style="background:linear-gradient(135deg,#2d5f9a,#4e86c2 55%,#1e3f6a)"></div>
    <h3>Business</h3>
    <p>Our Offshore development model has a unique distinction of providing efficient software solutions with cost and quality.....</p>
    <a class="btn">Read More</a>
  </div>
  <div class="card">
    <div class="photo" role="img" aria-label="Photo of a desk from above with keyboard, tablet, phone and coffee" style="background:linear-gradient(135deg,#d8dadc,#eceeef 50%,#b9bdc1)"></div>
    <h3>Application Developement</h3>
    <p>Drawing on our experience in all major industries, we develop solutions that meet the most challenging IT problems.</p>
    <a class="btn">Read More</a>
  </div>
</div>

<div class="abs partners"><span></span><span></span><span></span><span></span><span></span><span></span></div>

<footer class="abs footer">
  <div class="col" style="left:98px">
    <h4 style="position:static;margin-top:34px">About Beacon Advisory</h4>
    <div class="fbrand" style="left:0"><i></i>Beacon Advisory</div>
    <p class="ftext" style="position:absolute;top:150px;width:260px">Lorem ipsum dolor sit amet, consectetur adipiscing elit. Temporibus earum...<span style="color:#fff">Read More+</span></p>
  </div>
  <div class="col" style="left:449px">
    <h4 style="position:static;margin-top:34px">Menu</h4>
    <ul class="menu" style="margin-top:20px">
      <li>Home</li><li>Company</li><li>Services</li><li>Solutions</li><li>Resources</li><li>Career</li><li>Contact Us</li>
    </ul>
  </div>
  <div class="col" style="left:618px">
    <h4 style="position:static;margin-top:34px">Latest posts</h4>
    <div style="margin-top:20px">
      <div class="post">Lorem ipsum dolor sit amet, consectetur Temporibus earum atque...<b>March 02 2016</b></div>
      <div class="post">Lorem ipsum dolor sit amet, consectetur Temporibus earum atque...<b>March 02 2016</b></div>
    </div>
  </div>
  <div class="col" style="left:923px">
    <h4 style="position:static;margin-top:34px">Get in touch</h4>
    <div style="margin-top:20px">
      <div class="touch"><i></i><span>410 Harlow Ave Suite 12<br>Westbrook, NJ 07000</span></div>
      <div class="touch"><i></i><span>Phone: +1 (555) 014 2290</span></div>
      <div class="touch"><i></i><span>Mail:info@beaconadvisoryinc.com</span></div>
    </div>
  </div>
</footer>

<div class="abs bottom">
  <p>Copyrights©beaconadvisory.2016 | Allrights Reserved.</p>
  <div class="social"><span></span><span></span><span></span><span></span><span></span></div>
</div>

</body>
</html>
```